Telecommunications/Power civil contractor needs business card design

Were a new telecommunications/power underground civil contractor that is looking for a new business card design. Our company colours are silver or grey and orange. Feel free to use the white background logo or the black background logo.

Target Market(s)

Local contractors, utility companies, private sector mining/energy companies, developers.

Industry/Entity Type

Telecommunications

Contact Information for Business Card

Each card will need the following info:
Persons name:
Title:
E-mail:
Phone number:
Shop Address:
Mailing Address:

Requirements
Must have
• Each card will need the following info:
• Persons name:
• Title:
• E-mail:
• Phone number:
• Shop Address:
• Mailing Address:

```html
<!DOCTYPE html>
<html lang="en">
<head>
<meta charset="utf-8">
<title>Trenchline Civil Inc – Business Card</title>
<link rel="stylesheet" href="https://fonts.googleapis.com/css2?family=Pathway+Gothic+One&display=swap">
<style>
  :root {
    --canvas: #cfd4d4;
    --card: #0b0b0b;
    --card-band: #181818;
    --accent: #e2411c;
    --text-light: #e6e6e6;
    --text-muted: #bdbdbd;
    --divider: #5a1a0c;
  }
  html, body {
    margin: 0;
    width: 1200px;
    height: 1200px;
    overflow: hidden;
    background: var(--canvas);
  }
  .business-card {
    position: absolute;
    left: 75px;
    top: 300px;
    width: 1050px;
    height: 600px;
    background: var(--card);
    overflow: hidden;
    font-family: "Pathway Gothic One", "Arial Narrow", sans-serif;
    box-shadow: 0 20px 40px rgba(0,0,0,0.25);
  }
  .card-arc {
    position: absolute;
    inset: 0;
  }
  .shop-address {
    position: absolute;
    left: 42px;
    bottom: 24px;
    transform-origin: left bottom;
    transform: rotate(-90deg);
    white-space: nowrap;
    color: var(--text-light);
    font-size: 30px;
    letter-spacing: 0.5px;
  }
  .brand {
    position: absolute;
    left: 0;
    right: 0;
    top: 80px;
    text-align: center;
  }
  .brand-circle {
    display: block;
    width: 130px;
    height: 130px;
    margin: 0 auto 20px;
    border: 6px solid var(--accent);
    border-radius: 50%;
    box-sizing: border-box;
  }
  .brand-name {
    color: var(--accent);
    font-size: 58px;
    letter-spacing: 3px;
    text-transform: uppercase;
    line-height: 1;
  }
  .person {
    position: absolute;
    right: 500px;
    top: 410px;
    text-align: right;
  }
  .person-name {
    color: var(--accent);
    font-size: 60px;
    line-height: 1;
    letter-spacing: 1px;
  }
  .person-title {
    color: var(--text-muted);
    font-size: 30px;
    margin-top: 6px;
  }
  .divider {
    position: absolute;
    left: 570px;
    top: 395px;
    width: 2px;
    height: 170px;
    background: var(--divider);
  }
  .contact {
    position: absolute;
    left: 595px;
    top: 392px;
    color: var(--text-light);
    font-size: 29px;
    line-height: 41px;
  }
  .contact-label {
    color: var(--accent);
    margin-right: 8px;
  }
</style>
</head>
<body>
  <div class="business-card">
    <svg class="card-arc" width="1050" height="600" viewBox="0 0 1050 600" aria-hidden="true">
      <circle cx="760" cy="720" r="690" fill="none" stroke="var(--card-band)" stroke-width="46"/>
    </svg>

    <div class="shop-address">123 Dummy St. Dummy Centre, Dummy 12345</div>

    <div class="brand">
      <span class="brand-circle"></span>
      <div class="brand-name">Trenchline Civil Inc</div>
    </div>

    <div class="person">
      <div class="person-name">JOHN DOE</div>
      <div class="person-title">Director</div>
    </div>

    <div class="divider"></div>

    <div class="contact">
      <div>Dummy city</div>
      <div>Dummy Country Land Dummy</div>
      <div><span class="contact-label">T .</span>1-234-567890</div>
      <div><span class="contact-label">E .</span>john@companyname.com</div>
    </div>
  </div>
</body>
</html>
```